Double Sided Flyer for 3D printing services company

We need a nice balanced flyer for our corporate handout. The attached is for concept only and not the final design. We think the attached examples have elements that balance nicely but the graphics are not good. We are attaching the logo from the corporate office for our new logo. We will add the company information after the final design is selected for web address, phone, mailing etc. Please leave room for that information in the design. Please ask any questions prior to submission. Our main focus is printing RUBBER 3D Parts and not plastic parts. The images selected should be focused on that. We also need to ensure the images are approved for use in a corporate flyer for content.

```html
<!DOCTYPE html>
<html lang="en">
<head>
<meta charset="utf-8">
<title>Veranto – 3D Printing Services Flyer</title>
<link href="https://fonts.googleapis.com/css2?family=Montserrat:wght@400;500;600;700;800;900&display=swap" rel="stylesheet">
<style>
  :root {
    --orange: #cf5f2c;
    --ink: #1c1c1c;
    --charcoal: #2b2b2b;
    --slate: #4a4a4a;
    --ring: #6c6c6c;
    --mist: #f2f2f2;
    --white: #ffffff;
    --stage: #d4d4d4;
  }
  * { box-sizing: border-box; margin: 0; padding: 0; }
  html, body { width: 882px; height: 1200px; overflow: hidden; background: var(--stage); }
  body { position: relative; font-family: "Montserrat", sans-serif; }

  .page {
    position: absolute;
    top: 303px;
    width: 712px;
    height: 1005px;
    overflow: hidden;
    transform: scale(0.59);
    transform-origin: 0 0;
  }
  .page-front {
    left: 12px;
    background: linear-gradient(180deg, var(--mist) 0%, #e4e4e4 20%, #a6a6a6 30%, #474747 40%, var(--charcoal) 50%, var(--charcoal) 100%);
  }
  .page-back {
    left: 450px;
    background: linear-gradient(180deg, var(--white) 0%, #f8f8f8 16%, #9c9c9c 32%, #3c3c3c 44%, var(--charcoal) 55%, #262626 93%);
  }
  .artwork { position: absolute; inset: 0; }

  /* ---------- front ---------- */
  .brand { position: absolute; left: 34px; top: 46px; display: flex; align-items: center; gap: 10px; }
  .brand-dot { width: 36px; height: 36px; border-radius: 50%; background: var(--orange); }
  .brand-name { font-weight: 900; font-size: 38px; line-height: 1; color: var(--slate); letter-spacing: 0.5px; }
  .brand-tagline { position: absolute; left: 82px; top: 88px; font-weight: 600; font-size: 11px; letter-spacing: 1.4px; color: var(--slate); }

  .headline { position: absolute; left: 34px; top: 228px; }
  .headline-3d { font-weight: 900; font-size: 226px; line-height: 0.9; letter-spacing: -10px; }
  .headline-3d .three { color: var(--ink); -webkit-text-stroke: 5px #9a9a9a; paint-order: stroke fill; }
  .headline-3d .dee { color: var(--orange); -webkit-text-stroke: 5px #9a9a9a; paint-order: stroke fill; }
  .headline-printing { margin-top: -6px; font-weight: 800; font-size: 56px; line-height: 1; color: var(--orange); letter-spacing: -0.5px; }
  .headline-services { margin-top: 4px; font-weight: 900; font-size: 64px; line-height: 1; color: var(--white); letter-spacing: -1px; }

  .benefit-label {
    position: absolute;
    width: 206px; height: 48px;
    padding: 0 10px;
    display: flex; align-items: center;
    background: var(--slate);
    color: var(--white);
    font-weight: 800; font-size: 13px; line-height: 1.2;
    text-transform: uppercase;
  }
  .benefit-label.is-right { width: 152px; }

  .footer-rule { position: absolute; left: 30px; right: 28px; top: 944px; height: 2px; background: var(--orange); }
  .contact { position: absolute; top: 958px; height: 40px; display: flex; align-items: center; font-size: 13.5px; white-space: nowrap; }
  .contact-phone { left: 60px; display: block; top: 960px; }
  .contact-phone .lead { font-size: 12.5px; font-weight: 400; line-height: 1.2; }
  .contact-phone .number { font-size: 20px; font-weight: 800; line-height: 1.1; }
  .contact-email { left: 348px; }
  .contact-web { left: 560px; }
  .contact-divider { position: absolute; top: 954px; width: 1px; height: 46px; }

  .page-front .contact { color: var(--white); }
  .page-front .contact-phone .number { color: var(--orange); }
  .page-front .contact-divider { background: #6a6a6a; }

  /* ---------- back ---------- */
  .intro-title { position: absolute; left: 46px; top: 38px; font-weight: 800; font-size: 44px; line-height: 50px; color: var(--orange); letter-spacing: -0.5px; }
  .intro-title .accent { color: #3d3d3d; }
  .intro-copy { position: absolute; left: 48px; top: 144px; width: 624px; font-size: 12.5px; line-height: 17px; color: #222; font-weight: 500; }
  .check-list { position: absolute; left: 62px; top: 216px; list-style: none; }
  .check-list li { position: relative; padding-left: 22px; height: 23px; font-size: 12.5px; font-weight: 500; color: var(--white); line-height: 18px; }
  .check-list li svg { position: absolute; left: 0; top: 4px; }

  .benefits-title { position: absolute; left: 46px; top: 432px; font-weight: 800; font-size: 45px; line-height: 1; color: var(--orange); letter-spacing: -0.5px; white-space: nowrap; }
  .benefits-title .accent { color: var(--white); }

  .feature { position: absolute; left: 202px; width: 460px; }
  .feature-title { font-weight: 800; font-size: 25px; line-height: 1; color: var(--orange); }
  .feature-copy { margin-top: 9px; font-size: 12.5px; line-height: 17px; color: #e6e6e6; }

  .back-footer { position: absolute; left: 0; right: 0; top: 939px; bottom: 0; background: var(--white); border-top: 6px solid var(--orange); }
  .page-back .contact { color: #222; }
  .page-back .contact-phone .lead { color: var(--orange); }
  .page-back .contact-phone .number { color: #222; }
  .page-back .contact-divider { background: #9a9a9a; }
</style>
</head>
<body>

<!-- ================= FRONT ================= -->
<section class="page page-front">
  <svg class="artwork" width="712" height="1005" viewBox="0 0 712 1005" xmlns="http://www.w3.org/2000/svg">
    <defs>
      <linearGradient id="printer-tones" x1="0" y1="0" x2="0" y2="1">
        <stop offset="0" stop-color="#d9dde6"/>
        <stop offset="0.35" stop-color="#8b8f9c"/>
        <stop offset="0.6" stop-color="#f2a531"/>
        <stop offset="0.78" stop-color="#4a86d4"/>
        <stop offset="1" stop-color="#2f6cc0"/>
      </linearGradient>
      <linearGradient id="rubber-tones" x1="0" y1="0" x2="1" y2="1">
        <stop offset="0" stop-color="#555"/>
        <stop offset="0.5" stop-color="#222"/>
        <stop offset="1" stop-color="#b9252b"/>
      </linearGradient>
      <linearGradient id="mesh-tones" x1="0" y1="0" x2="0" y2="1">
        <stop offset="0" stop-color="#c9d3df"/>
        <stop offset="0.55" stop-color="#e2502c"/>
        <stop offset="1" stop-color="#5c8fcf"/>
      </linearGradient>
      <linearGradient id="nozzle-tones" x1="0" y1="0" x2="0" y2="1">
        <stop offset="0" stop-color="#8a8f99"/>
        <stop offset="0.6" stop-color="#e3b52c"/>
        <stop offset="1" stop-color="#6d93c8"/>
      </linearGradient>
      <clipPath id="hero-clip"><circle cx="510" cy="262" r="222"/></clipPath>
    </defs>

    <g class="hero-frame">
      <polygon points="330,400 420,548 712,522 712,380" fill="#5e5e5e"/>
      <line x1="420" y1="548" x2="712" y2="521" stroke="var(--orange)" stroke-width="5"/>
      <circle cx="510" cy="262" r="262" fill="var(--ring)"/>
      <path d="M 262 160 A 268 268 0 0 1 712 86" fill="none" stroke="var(--orange)" stroke-width="5"/>
      <circle cx="510" cy="262" r="240" fill="#3a3a3a"/>
      <g role="img" aria-label="Photo of a 3D printer nozzle building a yellow part on a blue print bed">
        <rect x="280" y="30" width="460" height="470" fill="url(#printer-tones)" clip-path="url(#hero-clip)"/>
      </g>
      <g fill="var(--white)">
        <circle cx="340" cy="73" r="9"/>
        <circle cx="262" cy="199" r="11"/>
        <circle cx="496" cy="482" r="18"/>
        <circle cx="699" cy="518" r="13"/>
      </g>
    </g>

    <g class="sample-bubbles">
      <g>
        <polygon points="104,724 141,732 108,758" fill="var(--white)"/>
        <ellipse cx="146" cy="662" rx="104" ry="76" fill="#1a1a1a"/>
        <ellipse cx="146" cy="662" rx="96" ry="68" fill="url(#rubber-tones)" stroke="var(--white)" stroke-width="7" role="img" aria-label="Photo of black and red rubber seals and gaskets"/>
        <circle cx="176" cy="734" r="3.5" fill="var(--orange)"/>
      </g>
      <g>
        <polygon points="314,724 351,732 318,758" fill="var(--white)"/>
        <ellipse cx="356" cy="662" rx="104" ry="76" fill="#1a1a1a"/>
        <ellipse cx="356" cy="662" rx="96" ry="68" fill="url(#mesh-tones)" stroke="var(--white)" stroke-width="7" role="img" aria-label="Photo of a red printed lattice part on a print bed"/>
        <circle cx="386" cy="734" r="3.5" fill="var(--orange)"/>
      </g>
      <g>
        <polygon points="527,724 564,732 531,758" fill="var(--white)"/>
        <ellipse cx="569" cy="662" rx="104" ry="76" fill="#1a1a1a"/>
        <ellipse cx="569" cy="662" rx="96" ry="68" fill="url(#nozzle-tones)" stroke="var(--white)" stroke-width="7" role="img" aria-label="Photo of a print head building a small yellow column"/>
        <circle cx="599" cy="734" r="3.5" fill="var(--orange)"/>
      </g>
    </g>

    <g class="benefit-icons" fill="none" stroke="var(--orange)" stroke-width="2.5" stroke-linecap="round">
      <circle cx="89" cy="817" r="25"/>
      <circle cx="89" cy="817" r="17"/>
      <polyline points="89,807 89,817 97,822"/>
      <rect x="64" y="888" width="7" height="28"/>
      <rect x="76" y="895" width="7" height="21"/>
      <rect x="88" y="901" width="7" height="15"/>
      <rect x="100" y="906" width="7" height="10"/>
      <circle cx="76" cy="872" r="8"/>
      <polyline points="88,874 108,890 102,890"/>
      <circle cx="466" cy="817" r="24"/>
      <line x1="466" y1="817" x2="477" y2="806"/>
      <line x1="418" y1="810" x2="440" y2="810"/>
      <line x1="422" y1="819" x2="443" y2="819"/>
      <line x1="427" y1="828" x2="445" y2="828"/>
      <rect x="446" y="868" width="30" height="44" rx="3"/>
      <rect x="451" y="874" width="20" height="8"/>
      <line x1="452" y1="892" x2="470" y2="892"/>
      <line x1="452" y1="901" x2="470" y2="901"/>
      <circle cx="440" cy="902" r="9"/>
    </g>

    <g stroke="#bbbbbb" stroke-width="1.2" stroke-dasharray="4 4">
      <line x1="150" y1="855" x2="338" y2="855"/>
      <line x1="425" y1="855" x2="612" y2="855"/>
      <line x1="383" y1="797" x2="383" y2="927"/>
    </g>

    <g fill="none" stroke="var(--orange)" stroke-width="2.5">
      <rect x="34" y="962" width="18" height="32" rx="3"/>
      <line x1="40" y1="988" x2="46" y2="988"/>
      <circle cx="333" cy="980" r="8" fill="var(--orange)" stroke="none"/>
      <polyline points="329,977 333,981 337,977" stroke="var(--white)" stroke-width="1.5"/>
      <circle cx="543" cy="980" r="8"/>
      <ellipse cx="543" cy="980" rx="3.5" ry="8" stroke-width="1.4"/>
      <line x1="535" y1="980" x2="551" y2="980" stroke-width="1.4"/>
    </g>
  </svg>

  <header>
    <div class="brand">
      <span class="brand-dot"></span>
      <span class="brand-name">VERANTO</span>
    </div>
    <div class="brand-tagline">SEALS·GASKETS·HOSES</div>
  </header>

  <h1 class="headline">
    <div class="headline-3d"><span class="three">3</span><span class="dee">D</span></div>
    <div class="headline-printing">PRINTING</div>
    <div class="headline-services">SERVICES</div>
  </h1>

  <div class="benefit-label" style="left:145px; top:794px;">Reduce time to market<br>from weeks to hours</div>
  <div class="benefit-label" style="left:145px; top:869px;">Eliminate costly<br>design errors</div>
  <div class="benefit-label is-right" style="left:499px; top:794px;">Faster time<br>to market</div>
  <div class="benefit-label is-right" style="left:499px; top:869px;">Reduced R<br>and D budgets</div>

  <footer>
    <div class="footer-rule"></div>
    <div class="contact contact-phone">
      <div class="lead">for more information :</div>
      <div class="number">+91-000-555-0142</div>
    </div>
    <span class="contact-divider" style="left:286px;"></span>
    <div class="contact contact-email">info@veranto.com</div>
    <span class="contact-divider" style="left:494px;"></span>
    <div class="contact contact-web">www.veranto.com</div>
  </footer>
</section>

<!-- ================= BACK ================= -->
<section class="page page-back">
  <h2 class="intro-title">Redefine your industry<br>with <span class="accent">3D PRINTING</span></h2>
  <p class="intro-copy">Lorem Ipsum is simply dummy text of the printing and typesetting industry. Lorem Ipsum has been the industry's standard dummy text. Lorem Ipsum is simply dummy text of the printing and typesetting industry. Lorem Ipsum has been the industry's standard dummy text.</p>

  <ul class="check-list">
    <li><svg width="12" height="10" viewBox="0 0 12 10"><polyline points="1,5 4.5,8.5 11,1" fill="none" stroke="#cf5f2c" stroke-width="2.4"/></svg>Lorem ipsum dolor sit amet, consectetur adipiscing elit.</li>
    <li><svg width="12" height="10" viewBox="0 0 12 10"><polyline points="1,5 4.5,8.5 11,1" fill="none" stroke="#cf5f2c" stroke-width="2.4"/></svg>Nam faucibus arcu ac diam suscipit, vel aliquam nunc laoreet.</li>
    <li><svg width="12" height="10" viewBox="0 0 12 10"><polyline points="1,5 4.5,8.5 11,1" fill="none" stroke="#cf5f2c" stroke-width="2.4"/></svg>Maecenas rutrum orci a imperdiet faucibus.</li>
    <li><svg width="12" height="10" viewBox="0 0 12 10"><polyline points="1,5 4.5,8.5 11,1" fill="none" stroke="#cf5f2c" stroke-width="2.4"/></svg>Maecenas malesuada mi et felis tempus laoreet.</li>
    <li><svg width="12" height="10" viewBox="0 0 12 10"><polyline points="1,5 4.5,8.5 11,1" fill="none" stroke="#cf5f2c" stroke-width="2.4"/></svg>Lorem ipsum dolor sit amet, consectetur adipiscing elit.</li>
    <li><svg width="12" height="10" viewBox="0 0 12 10"><polyline points="1,5 4.5,8.5 11,1" fill="none" stroke="#cf5f2c" stroke-width="2.4"/></svg>Nam faucibus arcu ac diam suscipit, vel aliquam nunc laoreet.</li>
    <li><svg width="12" height="10" viewBox="0 0 12 10"><polyline points="1,5 4.5,8.5 11,1" fill="none" stroke="#cf5f2c" stroke-width="2.4"/></svg>Maecenas rutrum orci a imperdiet faucibus.</li>
    <li><svg width="12" height="10" viewBox="0 0 12 10"><polyline points="1,5 4.5,8.5 11,1" fill="none" stroke="#cf5f2c" stroke-width="2.4"/></svg>Maecenas malesuada mi et felis tempus laoreet.</li>
  </ul>

  <h2 class="benefits-title">BENEFITS OF <span class="accent">3D PRINTING</span></h2>

  <svg class="artwork" width="712" height="1005" viewBox="0 0 712 1005" xmlns="http://www.w3.org/2000/svg">
    <g class="feature-badges" fill="none" stroke="var(--white)" stroke-width="4">
      <ellipse cx="105" cy="549" rx="58" ry="42"/>
      <polygon points="70,584 96,590 66,606" fill="var(--white)" stroke="none"/>
      <ellipse cx="105" cy="640" rx="58" ry="42"/>
      <polygon points="70,675 96,681 66,697" fill="var(--white)" stroke="none"/>
      <ellipse cx="105" cy="732" rx="58" ry="42"/>
      <polygon points="70,767 96,773 66,789" fill="var(--white)" stroke="none"/>
      <ellipse cx="105" cy="822" rx="58" ry="42"/>
      <polygon points="70,857 96,863 66,879" fill="var(--white)" stroke="none"/>
    </g>
    <g class="feature-icons" fill="none" stroke="var(--orange)" stroke-width="4" stroke-linecap="round">
      <path d="M 77 558 A 28 28 0 0 1 133 558"/>
      <line x1="105" y1="558" x2="116" y2="542"/>
      <circle cx="105" cy="558" r="5" fill="var(--orange)"/>
      <circle cx="102" cy="642" r="16"/>
      <line x1="102" y1="633" x2="102" y2="651" stroke-width="3"/>
      <polyline points="122,628 122,646 116,640" stroke-width="3"/>
      <rect x="82" y="736" width="14" height="14" fill="var(--orange)" stroke="none"/>
      <rect x="96" y="726" width="14" height="24" fill="var(--orange)" stroke="none"/>
      <rect x="110" y="740" width="14" height="10" fill="var(--orange)" stroke="none"/>
      <polyline points="103,718 103,705 97,711 103,705 109,711" stroke-width="3"/>
      <path d="M 93 828 A 14 14 0 1 1 117 828 L 114 836 L 96 836 Z" stroke-width="3"/>
      <line x1="98" y1="842" x2="112" y2="842" stroke-width="3"/>
    </g>
  </svg>

  <div class="feature" style="top:522px;">
    <div class="feature-title">SPEED TIME TO MARKET</div>
    <p class="feature-copy">Lorem Ipsum is simply dummy text of the printing and typesetting industry. Lorem Ipsum has been the industry's standard dummy text.</p>
  </div>
  <div class="feature" style="top:613px;">
    <div class="feature-title">SPEED TIME TO MARKET</div>
    <p class="feature-copy">Lorem Ipsum is simply dummy text of the printing and typesetting industry. Lorem Ipsum has been the industry's standard dummy text.</p>
  </div>
  <div class="feature" style="top:704px;">
    <div class="feature-title">SPEED TIME TO MARKET</div>
    <p class="feature-copy">Lorem Ipsum is simply dummy text of the printing and typesetting industry. Lorem Ipsum has been the industry's standard dummy text.</p>
  </div>
  <div class="feature" style="top:795px; width:370px;">
    <div class="feature-title">SPEED TIME TO MARKET</div>
    <p class="feature-copy">Lorem Ipsum is simply dummy text of the printing and typesetting industry. Lorem Ipsum has been the industry's standard dummy text.</p>
  </div>

  <footer>
    <div class="back-footer"></div>
    <svg class="artwork" width="712" height="1005" viewBox="0 0 712 1005" xmlns="http://www.w3.org/2000/svg">
      <g fill="none" stroke="var(--orange)" stroke-width="2.5">
        <rect x="34" y="962" width="18" height="32" rx="3"/>
        <line x1="40" y1="988" x2="46" y2="988"/>
        <circle cx="332" cy="980" r="8" fill="var(--orange)" stroke="none"/>
        <polyline points="328,977 332,981 336,977" stroke="var(--white)" stroke-width="1.5"/>
        <circle cx="541" cy="980" r="8"/>
        <ellipse cx="541" cy="980" rx="3.5" ry="8" stroke-width="1.4"/>
        <line x1="533" y1="980" x2="549" y2="980" stroke-width="1.4"/>
      </g>
    </svg>
    <div class="contact contact-phone">
      <div class="lead">for more information :</div>
      <div class="number">+91-000-555-0142</div>
    </div>
    <span class="contact-divider" style="left:286px;"></span>
    <div class="contact contact-email">info@veranto.com</div>
    <span class="contact-divider" style="left:493px;"></span>
    <div class="contact contact-web">www.veranto.com</div>
  </footer>
</section>

</body>
</html>
```